International pain relief company needs flyer designed

We are based in South Australia, and are about to launch a brand new hand held portable fully chargeable pain relief device. This device gives the user proven instant relief often from the first time of use anywhere. We intend to offer, a try before you buy at home /office demonstration, a full 30 day money back guarantee and a full 3 year warranty. We also plan to give the first 7 people who book a demonstration a FREE $20 Norvane fuel card.
We are open minded regarding the overall design and colours used, however we are particularly keen on seeing pictures/cartoons of people suffering from the 3 main groups of pain, head ache, back ache and joint pain, perhaps also happy faces once they have been cured/relieved by our equipment. This product we expect to retail for around the $300 AUD mark.
The wording on the leaflet is
Suffering from headaches, back ache or joint problems?
At last....there is instant pain relief!
New to Australia, a personal portable pain relief device
Call Ned 0427581963 & 08 74925183
PLR Australia PO Box 612, Elmhurst SA 5093

Target Market(s)

aged, elderly

Industry/Entity Type

Retail

Font styles to use
Serif
Sans Serif

Colors
33b7a4
33a6d7
3176b5

Requirements
Must have
• include Free in house/office demonstration
Free $20 Norvan fuel card for first 11 demonstrations
Nice to have
• Norvane fuel logo

```html
<!DOCTYPE html>
<html lang="en">
<head>
<meta charset="utf-8">
<title>PLR Australia – Portable Pain Relief Flyer</title>
<link href="https://fonts.googleapis.com/css2?family=Oswald:wght@500;600;700&display=swap" rel="stylesheet">
<style>
  :root {
    --navy-ink: #0f1a4a;
    --blue-deep: #1b2c86;
    --blue-mid: #2d5cc4;
    --blue-bright: #3a7fe0;
    --orange-light: #f9a12b;
    --orange-dark: #f0581f;
    --white: #ffffff;
    --photo-skin: #e7c3a8;
    --photo-light: #d9e3ea;
  }
  * { margin: 0; padding: 0; box-sizing: border-box; }
  html, body { width: 933px; height: 1200px; overflow: hidden; background: #ffffff; }
  .flyer {
    position: relative;
    width: 933px;
    height: 1200px;
    overflow: hidden;
    background: radial-gradient(ellipse at 55% 45%, var(--blue-bright) 0%, var(--blue-mid) 40%, var(--blue-deep) 100%);
    font-family: "Oswald", "Arial Narrow", sans-serif;
    font-weight: 600;
    text-transform: uppercase;
    color: var(--navy-ink);
  }
  .banner {
    position: absolute;
    background: linear-gradient(90deg, var(--orange-light), var(--orange-dark));
    box-shadow: 0 6px 14px rgba(0,0,0,0.35);
    text-align: center;
    line-height: 1.12;
  }
  .banner--question {
    left: 370px; top: 118px; width: 526px; height: 172px;
    border-radius: 30px;
    padding-top: 16px; padding-left: 56px;
    font-size: 45px;
  }
  .banner--relief {
    left: 30px; top: 407px; width: 560px; height: 200px;
    border-radius: 30px;
    padding-top: 14px; padding-right: 20px;
  }
  .relief-title { font-size: 46px; line-height: 1.08; font-weight: 700; }
  .relief-sub { font-size: 33px; line-height: 1.15; margin-top: 6px; }
  .photo {
    position: absolute;
    border-radius: 50%;
    border: 7px solid var(--white);
    box-shadow: 0 4px 12px rgba(0,0,0,0.4);
  }
  .photo--headache { left: 22px; top: -8px; width: 164px; height: 164px; background: linear-gradient(135deg, #f4e2c6, var(--photo-skin) 60%, var(--photo-light)); }
  .photo--knee { left: 200px; top: 7px; width: 178px; height: 178px; background: linear-gradient(135deg, var(--photo-light), #c99a7c 55%, #b47a5d); }
  .photo--back { left: 101px; top: 182px; width: 184px; height: 184px; background: radial-gradient(circle at 45% 45%, #d9553c 0%, #c98a6a 30%, var(--photo-skin) 70%, #f1f1f1); }
  .photo--smile { left: 540px; top: 385px; width: 164px; height: 164px; background: linear-gradient(135deg, #dfe8ee, #f1d7c0 50%, #e6c193); }
  .photo--couple { left: 714px; top: 366px; width: 172px; height: 172px; background: linear-gradient(135deg, #e9eef2, #d9b7a0 50%, #5b7aa0); }
  .photo--pair { left: 619px; top: 464px; width: 184px; height: 184px; background: linear-gradient(135deg, #e2e6e8, #d7a98a 50%, #9c3a2e); }
  .contact {
    position: absolute; color: var(--white);
  }
  .contact--call { left: 33px; top: 647px; font-size: 32px; letter-spacing: 0.5px; }
  .contact--address { left: 100px; top: 737px; width: 420px; text-align: center; font-size: 28px; line-height: 1.3; }
  .bottom-wave { position: absolute; left: 0; top: 0; }
  .offer {
    position: absolute; left: 0; top: 877px; width: 726px;
    text-align: center; font-size: 28px; line-height: 1.33;
  }
  .offer p + p { margin-top: 16px; }
  .badge {
    position: absolute; border-radius: 50%;
    background: radial-gradient(circle at 40% 35%, var(--blue-bright), var(--blue-deep));
    border: 7px solid var(--white);
    box-shadow: 0 0 0 5px var(--blue-deep), 0 6px 14px rgba(0,0,0,0.4);
    color: var(--white);
    display: flex; align-items: center; justify-content: center;
  }
  .badge--warranty { left: 537px; top: 700px; width: 214px; height: 214px; }
  .badge--fuel { left: 681px; top: 815px; width: 222px; height: 222px; }
  .warranty-mark { display: flex; align-items: center; transform: rotate(-15deg); }
  .warranty-number { font-size: 112px; font-weight: 700; line-height: 1; }
  .warranty-words { font-size: 30px; line-height: 0.95; margin-left: 4px; }
  .warranty-words span:last-child { font-size: 22px; }
  .fuel-mark { text-align: center; transform: rotate(12deg); line-height: 1; }
  .fuel-free { font-size: 46px; font-weight: 700; }
  .fuel-amount { font-size: 64px; font-weight: 700; }
  .fuel-amount sup { font-size: 34px; vertical-align: 24px; }
  .fuel-card { font-size: 24px; line-height: 1.05; margin-top: 4px; }
</style>
</head>
<body>
<div class="flyer">
  <div class="banner banner--question">Suffering from<br>headaches, back ache<br>or joint problems?</div>
  <div class="photo photo--headache" role="img" aria-label="Photo of a woman holding her head with a headache"></div>
  <div class="photo photo--knee" role="img" aria-label="Photo of hands clutching a sore knee"></div>
  <div class="photo photo--back" role="img" aria-label="Photo of a man's back with lower back pain highlighted in red"></div>

  <div class="banner banner--relief">
    <div class="relief-title">At last.....there is<br>instant pain relief!</div>
    <div class="relief-sub">New to Australia, a personal<br>portable pain relief device</div>
  </div>
  <div class="photo photo--smile" role="img" aria-label="Photo of a smiling young woman"></div>
  <div class="photo photo--couple" role="img" aria-label="Photo of a happy elderly couple relaxing"></div>
  <div class="photo photo--pair" role="img" aria-label="Photo of a smiling older couple"></div>

  <div class="contact contact--call">Call Ned 0427581963 &amp; 08 74925183</div>
  <div class="contact contact--address">PLR Australia PO Box 612,<br>Elmhurst SA 5093</div>

  <svg class="bottom-wave" width="933" height="1200" viewBox="0 0 933 1200" aria-hidden="true">
    <defs>
      <linearGradient id="offerOrange" x1="0" y1="0" x2="1" y2="0">
        <stop offset="0" stop-color="#f9a12b"/>
        <stop offset="1" stop-color="#f0581f"/>
      </linearGradient>
    </defs>
    <path d="M0,883 C220,826 560,830 933,1056 L933,1200 L0,1200 Z" fill="#0b1340" opacity="0.55"/>
    <path d="M0,893 C220,836 560,840 933,1066 L933,1200 L0,1200 Z" fill="url(#offerOrange)"/>
  </svg>

  <div class="offer">
    <p>Try before you buy<br>at home/office demonstration,<br>a full 30 day money back guarantee<br>and a full 3 year warranty.</p>
    <p>We also plan to give the first 7 people<br>who book a demonstration<br>a free $20 Norvane fuel card.</p>
  </div>

  <div class="badge badge--warranty">
    <div class="warranty-mark">
      <span class="warranty-number">3</span>
      <span class="warranty-words"><span>Year</span><br><span>Warranty</span></span>
    </div>
  </div>
  <div class="badge badge--fuel">
    <div class="fuel-mark">
      <div class="fuel-free">Free</div>
      <div class="fuel-amount"><sup>$</sup>20</div>
      <div class="fuel-card">Norvane<br>fuel card</div>
    </div>
  </div>
</div>
</body>
</html>
```